Spring Detox sale graphics for social media

You MUST read the Brief in the WORD document and follow the instructions there. I want to create 10 social media graphics (new Instagram size 4:5 (1080 x 1350 pixels) focusing on our Mother’s Day Spring Detox Sale graphics, using any of the pics attached. Use the attached pics, NO RANDOM STOCK PHOTOGRAPHY. For the color scheme of the graphics, they should all be complementary to the product colors or feel like Spring time.

Target Market(s)

primarily women

Requirements
Must have
• the photos and text attached

```html
<!DOCTYPE html>
<html lang="en">
<head>
<meta charset="utf-8">
<title>Mother's Day Spring Detox Sale – Social Set</title>
<link rel="stylesheet" href="https://fonts.googleapis.com/css2?family=Oswald:wght@500;600;700&family=Anton&family=Montserrat:ital,wght@0,700;0,800;0,900;1,800&family=Poppins:wght@600;700&family=Great+Vibes&display=swap">
<style>
:root{
  --stage:#343434;
  --cream:#fdf3ea;
  --forest:#1f4a3d;
  --mint:#a8d5c6;
  --mint-light:#a9d6c8;
  --sage:#6f9a80;
  --sage-deep:#3e7a5d;
  --pale-green:#eef2ec;
  --rose:#d9609a;
  --hot-pink:#ff4473;
  --pink:#e8418f;
  --plum:#a04b7c;
  --berry:#b5295e;
  --orchid:#a83d83;
  --magenta:#d6269f;
  --crimson:#b52a35;
  --red:#e0202a;
  --cocoa:#4a2b22;
  --brick:#a3242a;
  --ink:#1b1b1b;
  --white:#ffffff;
}
*{margin:0;padding:0;box-sizing:border-box}
html,body{width:1200px;height:2975px;overflow:hidden;background:var(--stage)}
.sheet{position:relative;width:1200px;height:2975px}
.post{position:absolute;width:393px;height:491px;overflow:hidden}
.col-a{left:187px}.col-b{left:619px}
.row-1{top:173px}.row-2{top:698px}.row-3{top:1222px}.row-4{top:1746px}.row-5{top:2271px}
.post>*{position:absolute}
.post p{white-space:nowrap;z-index:2}
.cond{font-family:"Oswald",sans-serif;font-weight:700;text-transform:uppercase;line-height:1;letter-spacing:-1px}
.heavy{font-family:"Anton",sans-serif;line-height:1;text-transform:uppercase}
.wide{font-family:"Montserrat",sans-serif;font-weight:900;line-height:1;text-transform:uppercase}
.script{font-family:"Great Vibes",cursive;line-height:1}
.center{left:0;right:0;text-align:center}
.bottles{background:linear-gradient(180deg,#f4f4f4 0%,#e6e3e6 55%,#c9c4cc 100%);border-radius:14px 14px 4px 4px;z-index:1}

/* 1 */
.p1{background:var(--cream)}
.p1 .art-hero{left:0;top:0;width:230px;height:190px;background:radial-gradient(ellipse at 35% 40%,#7a1f22 0%,#c0575f 45%,rgba(240,170,180,.4) 75%,rgba(253,243,234,0) 100%)}
.p1 .title-script{left:215px;top:50px;font-size:42px;color:var(--ink);width:170px;text-align:center;line-height:1.2}
.p1 .lead{top:176px;font-size:60px;color:var(--forest)}
.p1 .big{top:238px;font-size:188px;color:var(--forest)}
.p1 .foot{top:432px;font-size:40px;color:var(--forest)}

/* 2 */
.p2{background:var(--cream)}
.p2 .art-hero{left:225px;top:0;width:168px;height:235px;background:linear-gradient(160deg,#f3b7c6 0%,#8a6fb0 50%,#2d2f6a 100%);opacity:.85}
.p2 .pct{left:20px;top:20px;font-size:96px;color:var(--forest);letter-spacing:-3px}
.p2 .off{left:22px;top:134px;font-size:58px;color:var(--forest)}
.p2 .occasion{left:28px;top:202px;font-family:"Montserrat",sans-serif;font-weight:800;font-size:34px;color:var(--crimson)}
.p2 .panel{left:7px;top:245px;width:371px;height:177px;background:var(--forest);border-top-left-radius:62px}
.p2 .panel-lead{left:7px;width:371px;top:268px;text-align:center;font-family:"Montserrat",sans-serif;font-weight:800;font-size:34px;color:var(--mint-light)}
.p2 .panel-big{left:7px;width:371px;top:305px;text-align:center;font-size:72px;color:var(--white);letter-spacing:2px}
.p2 .bottles{left:30px;top:380px;width:330px;height:111px}

/* 3 */
.p3{background:var(--rose)}
.p3 .corner{left:220px;top:0;width:173px;height:160px;background:linear-gradient(135deg,#fbe9ef,#f2bfd2);border-bottom-left-radius:60px}
.p3 .pct{left:36px;top:36px;font-size:72px;color:var(--white)}
.p3 .off{left:36px;top:118px;font-size:88px;color:var(--white)}
.p3 .photo{left:0;top:240px;width:215px;height:251px;background:linear-gradient(180deg,#7a4a35 0%,#b88a6e 55%,#e8e2dc 100%)}
.p3 .stack{left:218px;width:168px;top:196px;text-align:center;font-size:55px;line-height:1.3;color:var(--white)}
.p3 .strip{left:99px;top:452px;font-size:38px;color:var(--white)}

/* 4 */
.p4{background:var(--mint)}
.p4 .pct{top:24px;font-size:74px;color:var(--forest)}
.p4 .lead{top:104px;font-size:62px;color:var(--forest)}
.p4 .box{left:19px;top:190px;width:354px;height:176px;background:var(--forest)}
.p4 .box-lead{left:40px;top:205px;font-size:44px;line-height:1.05;color:var(--white)}
.p4 .box-big{left:178px;top:200px;font-size:100px;color:var(--white)}
.p4 .bottles{left:40px;top:308px;width:315px;height:127px}
.p4 .tag{top:440px;font-family:"Montserrat",sans-serif;font-style:italic;font-weight:800;font-size:38px;color:var(--forest)}

/* 5 */
.p5{background:var(--white)}
.p5 .wave{left:0;top:0}
.p5 .pct{top:20px;font-size:90px;color:var(--white)}
.p5 .lead{top:128px;font-size:76px;color:var(--white)}
.p5 .art-hero{left:40px;top:205px;width:125px;height:150px;background:linear-gradient(180deg,#fff 0%,#ffd7e1 100%);border-radius:60px 60px 0 0}
.p5 .bottles{left:165px;top:255px;width:215px;height:90px}
.p5 .occasion{top:368px;font-size:64px;color:var(--hot-pink)}
.p5 .foot{top:438px;font-family:"Poppins",sans-serif;font-weight:700;font-size:31px;color:var(--ink)}

/* 6 */
.p6{background:var(--white)}
.p6 .art-hero{left:225px;top:15px;width:145px;height:165px;background:radial-gradient(circle at 50% 45%,#f06aa6 0%,#f7b2cf 55%,rgba(255,255,255,0) 80%)}
.p6 .occasion{left:15px;width:190px;top:27px;text-align:center;font-size:52px;line-height:1.05;color:var(--pink)}
.p6 .big{left:15px;width:190px;top:148px;text-align:center;font-size:96px;color:var(--pink)}
.p6 .badge{left:228px;top:160px;width:158px;height:158px;border-radius:50%;background:var(--plum);z-index:2}
.p6 .ring{left:233px;top:165px;width:148px;height:148px;border-radius:50%;border:2px dashed rgba(255,255,255,.7);z-index:2}
.p6 .badge-text{left:228px;width:158px;top:192px;text-align:center;font-size:48px;line-height:1.05;color:var(--white);z-index:3}
.p6 .bottles{left:30px;top:300px;width:315px;height:120px}
.p6 .tag{left:36px;top:428px;font-family:"Oswald",sans-serif;font-weight:600;font-size:37px;color:var(--berry)}

/* 7 */
.p7 .photo{left:0;top:0;width:393px;height:491px;background:linear-gradient(180deg,#e7eaec 0%,#e7eaec 55%,#5a3c2c 58%,#6b4a36 80%,#e6e2de 84%,#f2f0ee 100%)}
.p7 .pct{left:14px;top:34px;font-size:76px;color:var(--cocoa)}
.p7 .off-v{left:-40px;top:160px;font-size:96px;color:var(--cocoa);transform:rotate(-90deg);transform-origin:center}
.p7 .occasion{right:6px;top:48px;text-align:right;font-size:36px;line-height:1.15;color:var(--brick)}
.p7 .occasion .day{font-size:52px}
.p7 .sale-v{right:-22px;top:185px;font-size:92px;color:var(--cocoa);transform:rotate(-90deg)}
.p7 .foot{top:432px;font-size:44px;color:var(--cocoa)}

/* 8 */
.p8{background:linear-gradient(160deg,#f3f6f1 0%,var(--pale-green) 60%,#e3ebe2 100%)}
.p8 .pct{left:30px;top:30px;font-size:136px;color:var(--forest);letter-spacing:-3px}
.p8 .off-v{left:300px;top:58px;font-size:70px;color:var(--forest);transform:rotate(90deg)}
.p8 .rule{left:19px;width:355px;height:3px;background:var(--forest)}
.p8 .r1{top:175px}.p8 .r2{top:339px}
.p8 .lead{top:190px;font-size:58px;color:var(--sage)}
.p8 .big{top:254px;font-size:80px;color:var(--sage);letter-spacing:4px}
.p8 .l1{top:347px;font-size:54px;color:var(--forest)}
.p8 .l2{top:405px;font-size:60px;color:var(--forest)}

/* 9 */
.p9{background:var(--white)}
.p9 .wave{left:0;top:0}
.p9 .title-script{left:28px;top:6px;font-size:46px;color:var(--white)}
.p9 .big{left:32px;top:60px;font-size:88px;color:var(--white)}
.p9 .art-hero{left:235px;top:20px;width:150px;height:205px;background:linear-gradient(180deg,rgba(255,255,255,.95),#fbe3f2);border-radius:70px 70px 0 0}
.p9 .pct{left:18px;top:210px;font-family:"Montserrat",sans-serif;font-weight:800;font-size:54px;line-height:1.08;color:var(--red)}
.p9 .bottles{left:160px;top:195px;width:225px;height:135px}
.p9 .foot{top:362px;font-size:46px;line-height:1.1;color:var(--orchid)}

/* 10 */
.p10{background:linear-gradient(160deg,#f3f6f1 0%,var(--pale-green) 60%,#e3ebe2 100%)}
.p10 .pct{top:18px;font-size:100px;color:var(--forest);letter-spacing:-2px}
.p10 .lead{top:117px;font-size:46px;color:var(--forest)}
.p10 .bottles{left:30px;top:190px;width:315px;height:130px}
.p10 .l1{top:340px;font-size:62px;color:var(--sage-deep)}
.p10 .l2{top:412px;font-size:44px;color:var(--forest)}
</style>
</head>
<body>
<main class="sheet">

  <section class="post p1 col-a row-1">
    <div class="art-hero" role="img" aria-label="Watercolour silhouette of a mother lifting her child"></div>
    <p class="script title-script">Mother's<br>Day</p>
    <p class="cond center lead">Spring Detox</p>
    <p class="heavy center big">Sale</p>
    <p class="cond center foot">25% Off Everything!</p>
  </section>

  <section class="post p2 col-b row-1">
    <div class="art-hero" role="img" aria-label="Illustration of a mother hugging her child with hearts"></div>
    <p class="wide pct">25%</p>
    <p class="wide off">Off</p>
    <p class="occasion">MOTHER'S DAY</p>
    <div class="panel"></div>
    <p class="panel-lead">SPRING DETOX</p>
    <p class="wide panel-big">Sale</p>
    <div class="bottles" role="img" aria-label="Photo of four supplement bottles"></div>
  </section>

  <section class="post p3 col-a row-2">
    <div class="corner" role="img" aria-label="Illustration of a mother and child with pink flowers"></div>
    <p class="cond pct">25%</p>
    <p class="cond off">Off</p>
    <div class="photo" role="img" aria-label="Photo of a smiling woman in a kitchen with supplement bottles on the counter"></div>
    <p class="cond stack">Spring<br>Detox<br>Sale!</p>
    <p class="cond strip">All Supplements</p>
  </section>

  <section class="post p4 col-b row-2">
    <p class="wide center pct">25% Off</p>
    <p class="cond center lead">Spring Reset</p>
    <div class="box"></div>
    <p class="cond box-lead">Spring<br>Detox</p>
    <p class="cond box-big">Sale</p>
    <div class="bottles" role="img" aria-label="Photo of four supplement bottles"></div>
    <p class="center tag">Summer Ready</p>
  </section>

  <section class="post p5 col-a row-3">
    <svg class="wave" width="393" height="491" viewBox="0 0 393 491" aria-hidden="true">
      <path d="M0 0H393V325C330 330 260 345 200 352C120 362 60 350 0 330Z" fill="var(--hot-pink)"/>
    </svg>
    <p class="cond center pct">25% Off</p>
    <p class="cond center lead">Everything</p>
    <div class="art-hero" role="img" aria-label="Line silhouette of a mother and baby with hearts"></div>
    <div class="bottles" role="img" aria-label="Photo of four supplement bottles"></div>
    <p class="cond center occasion">Mother's Day</p>
    <p class="center foot">SPRING DETOX SALE</p>
  </section>

  <section class="post p6 col-b row-3">
    <div class="art-hero" role="img" aria-label="Pink watercolour silhouette of a mother and child"></div>
    <p class="cond occasion">Mother's<br>Day</p>
    <p class="cond big">Sale</p>
    <div class="bottles" role="img" aria-label="Photo of four supplement bottles"></div>
    <div class="badge"></div>
    <div class="ring"></div>
    <p class="cond badge-text">25%<br>Off</p>
    <p class="tag">Feel Amazing Again!</p>
  </section>

  <section class="post p7 col-a row-4">
    <div class="photo" role="img" aria-label="Photo of a smiling woman presenting supplement bottles on a marble counter"></div>
    <p class="cond pct">25%</p>
    <p class="cond off-v">Off</p>
    <p class="cond occasion">Mother's<br><span class="day">Day</span></p>
    <p class="cond sale-v">Sale</p>
    <p class="cond center foot">Refresh Your Body</p>
  </section>

  <section class="post p8 col-b row-4">
    <p class="cond pct">25%</p>
    <p class="cond off-v">Off</p>
    <div class="rule r1"></div>
    <p class="cond center lead">Spring Detox</p>
    <p class="wide center big">Sale</p>
    <div class="rule r2"></div>
    <p class="cond center l1">Spring Cleanse</p>
    <p class="cond center l2">Summer Glow</p>
  </section>

  <section class="post p9 col-a row-5">
    <svg class="wave" width="393" height="491" viewBox="0 0 393 491" aria-hidden="true">
      <defs><linearGradient id="magentaFade" x1="0" y1="0" x2="0" y2="1"><stop offset="0" stop-color="#d6269f"/><stop offset="1" stop-color="#c41f8d"/></linearGradient></defs>
      <path d="M0 0H393V200C330 185 280 175 220 185C150 198 70 190 0 170Z" fill="url(#magentaFade)"/>
    </svg>
    <div class="art-hero" role="img" aria-label="Silhouette of a mother tossing her child into the air"></div>
    <p class="script title-script">Mother's Day</p>
    <p class="cond big">Sale</p>
    <p class="pct">25%<br>OFF</p>
    <div class="bottles" role="img" aria-label="Photo of four supplement bottles"></div>
    <p class="cond center foot">Detox This Spring<br>Shine This Summer</p>
  </section>

  <section class="post p10 col-b row-5">
    <p class="cond center pct">25%Off</p>
    <p class="cond center lead">Mother's Day Sale</p>
    <div class="bottles" role="img" aria-label="Photo of four supplement bottles"></div>
    <p class="cond center l1">Spring Detox</p>
    <p class="cond center l2">For A Summer Body</p>
  </section>

</main>
</body>
</html>
```